I need a flyer made , the flyer can be one page or two pages or three pages . I will be posting this on Instagram and social media platforms. I am a luxury home builder , I am looking to hire a construction project manager . Below are some examples and ideas what can be on the flyer

We’re looking for a construction project manager who’s passionate about building luxury homes at the highest standards
We’re hiring construction project manager
* Experience 5+ years in residential project management with a strong portfolio of completed homes.
* location : Bergen County NJ
* excellent leadership skills, leads teams with confidence and clarity
* communicates seamlessly with architects , engineers, designers and clients
*knows how to manage budgets and timelines without compromising quality
*solves problems with a positive solution first mindset
* pays attention to every detail because in luxury the small things are the big things

Apply now , link in bio or DM to connect.

My logo is attached, my web site www.velstridebuilders.com
My style is modern but still warm and inviting. I like a clean classy look .

Please don’t add any images of chairs or people to the flyer , I do not want people on my flyer. Do not add standard images of offices and houses , we are luxury builders , we build homes over 2 million dollars. Keep a classy , simple modern look . High end .

You can add a white hard hat with my logo on it for a image , this is a suggestion does not have to be on my flyer ,

```html
<!DOCTYPE html>
<html lang="en">
<head>
<meta charset="utf-8">
<title>Velstride Builders – Hiring Construction Project Manager</title>
<link href="https://fonts.googleapis.com/css2?family=Montserrat:ital,wght@0,400;0,500;0,600;0,700;0,800;1,400;1,700&display=swap" rel="stylesheet">
<style>
  :root {
    --ink: #0d0d0d;
    --paper: #ffffff;
    --rule: #3a3a3a;
    --text: #161616;
  }
  * { margin: 0; padding: 0; box-sizing: border-box; }
  html, body { width: 1200px; height: 1200px; overflow: hidden; background: var(--paper); }
  body { font-family: "Montserrat", sans-serif; color: var(--text); }

  .flyer { position: relative; width: 1200px; height: 1200px; background: var(--paper); }

  .hero { position: absolute; left: 0; top: 0; width: 1200px; height: 565px; background: var(--ink); color: var(--paper); }
  .hero__kicker { position: absolute; top: 76px; width: 100%; text-align: center; font-weight: 700; font-size: 56px; letter-spacing: 0.18em; padding-left: 0.18em; line-height: 1; }
  .hero__title { position: absolute; top: 130px; width: 100%; text-align: center; font-weight: 800; font-size: 196px; letter-spacing: -3px; line-height: 1; }
  .hero__role-top { position: absolute; top: 316px; width: 100%; text-align: center; font-weight: 600; font-size: 34px; letter-spacing: 0.22em; padding-left: 0.22em; line-height: 1; }
  .hero__role { position: absolute; top: 346px; width: 100%; text-align: center; font-weight: 800; font-size: 49px; line-height: 1; }
  .hero__rule { position: absolute; left: 213px; width: 776px; height: 1px; background: var(--rule); }
  .hero__rule--top { top: 418px; }
  .hero__rule--bottom { top: 468px; }
  .hero__tagline { position: absolute; top: 427px; width: 100%; text-align: center; font-style: italic; font-weight: 400; font-size: 26px; letter-spacing: 0.06em; line-height: 1.1; }
  .hero__tagline strong { font-weight: 700; }
  .hero__location { position: absolute; top: 484px; width: 100%; text-align: center; line-height: 1; white-space: nowrap; }
  .hero__location-label { font-weight: 700; font-size: 38px; letter-spacing: 0.14em; margin-right: 18px; }
  .hero__location-value { font-weight: 700; font-size: 40px; }

  .requirement { position: absolute; width: 440px; }
  .requirement__icon { position: absolute; left: 0; top: 4px; width: 22px; height: 22px; }
  .requirement__title { margin-left: 33px; font-weight: 700; font-size: 23px; line-height: 1.1; color: var(--ink); }
  .requirement__body { margin-left: 33px; font-weight: 500; font-size: 18.5px; line-height: 1.26; color: var(--text); }
  .col-left { left: 147px; }
  .col-right { left: 650px; }

  .apply { position: absolute; left: 188px; top: 914px; width: 768px; height: 70px; border-radius: 35px; background: var(--ink); color: var(--paper); display: flex; align-items: center; justify-content: center; gap: 22px; white-space: nowrap; }
  .apply__label { font-weight: 800; font-size: 30px; }
  .apply__text { font-weight: 500; font-size: 28px; }

  .brand { position: absolute; left: 110px; top: 1074px; width: 372px; text-align: center; color: var(--ink); font-weight: 600; font-size: 34px; line-height: 1; white-space: nowrap; }

  .contact { position: absolute; left: 560px; top: 1040px; width: 560px; text-align: center; color: var(--ink); }
  .contact__social { display: flex; align-items: center; justify-content: center; gap: 12px; font-weight: 600; font-size: 26px; line-height: 1; }
  .contact__dot { width: 30px; height: 30px; border-radius: 50%; background: var(--ink); }
  .contact__web { margin-top: 20px; font-weight: 700; font-size: 33px; line-height: 1; }

  .base-bar { position: absolute; left: 91px; top: 1183px; width: 1019px; height: 17px; background: var(--ink); }
</style>
</head>
<body>
<main class="flyer">
  <section class="hero">
    <p class="hero__kicker">WE’RE</p>
    <h1 class="hero__title">HIRING</h1>
    <p class="hero__role-top">CONSTRUCTION</p>
    <h2 class="hero__role">PROJECT MANAGER</h2>
    <div class="hero__rule hero__rule--top"></div>
    <p class="hero__tagline">Build <strong>Luxury.</strong> Lead <strong>Excellence.</strong></p>
    <div class="hero__rule hero__rule--bottom"></div>
    <p class="hero__location"><span class="hero__location-label">LOCATION</span><span class="hero__location-value">Bergen County, NJ</span></p>
  </section>

  <div class="requirement col-left" style="top:620px">
    <svg class="requirement__icon" viewBox="0 0 22 22"><circle cx="11" cy="11" r="9.5" fill="none" stroke="#161616" stroke-width="2"/><path d="M6.8 11.2l3 3 5.6-6" fill="none" stroke="#161616" stroke-width="2" stroke-linecap="round" stroke-linejoin="round"/></svg>
    <p class="requirement__title">Experience 5+ years</p>
    <p class="requirement__body">in residential project management with<br>a strong portfolio of completed homes.</p>
  </div>
  <div class="requirement col-left" style="top:717px">
    <svg class="requirement__icon" viewBox="0 0 22 22"><circle cx="11" cy="11" r="9.5" fill="none" stroke="#161616" stroke-width="2"/><path d="M6.8 11.2l3 3 5.6-6" fill="none" stroke="#161616" stroke-width="2" stroke-linecap="round" stroke-linejoin="round"/></svg>
    <p class="requirement__title">Excellent leadership skills</p>
    <p class="requirement__body">leads teams with confidence and clarity</p>
  </div>
  <div class="requirement col-left" style="top:795px">
    <svg class="requirement__icon" viewBox="0 0 22 22"><circle cx="11" cy="11" r="9.5" fill="none" stroke="#161616" stroke-width="2"/><path d="M6.8 11.2l3 3 5.6-6" fill="none" stroke="#161616" stroke-width="2" stroke-linecap="round" stroke-linejoin="round"/></svg>
    <p class="requirement__title">Communicates seamlessly</p>
    <p class="requirement__body">with architects, engineers, designers<br>and clients</p>
  </div>

  <div class="requirement col-right" style="top:620px">
    <svg class="requirement__icon" viewBox="0 0 22 22"><circle cx="11" cy="11" r="9.5" fill="none" stroke="#161616" stroke-width="2"/><path d="M6.8 11.2l3 3 5.6-6" fill="none" stroke="#161616" stroke-width="2" stroke-linecap="round" stroke-linejoin="round"/></svg>
    <p class="requirement__title">Knows how to manage</p>
    <p class="requirement__body">budgets and timelines without<br>compromising quality</p>
  </div>
  <div class="requirement col-right" style="top:722px">
    <svg class="requirement__icon" viewBox="0 0 22 22"><circle cx="11" cy="11" r="9.5" fill="none" stroke="#161616" stroke-width="2"/><path d="M6.8 11.2l3 3 5.6-6" fill="none" stroke="#161616" stroke-width="2" stroke-linecap="round" stroke-linejoin="round"/></svg>
    <p class="requirement__title">Solves problems</p>
    <p class="requirement__body">with a positive solution first mindset</p>
  </div>
  <div class="requirement col-right" style="top:799px">
    <svg class="requirement__icon" viewBox="0 0 22 22"><circle cx="11" cy="11" r="9.5" fill="none" stroke="#161616" stroke-width="2"/><path d="M6.8 11.2l3 3 5.6-6" fill="none" stroke="#161616" stroke-width="2" stroke-linecap="round" stroke-linejoin="round"/></svg>
    <p class="requirement__title">Pays attention to every detail</p>
    <p class="requirement__body">because in luxury the small things are<br>the big things</p>
  </div>

  <div class="apply">
    <span class="apply__label">APPLY NOW</span>
    <span class="apply__text">Link in Bio or DM to connect.</span>
  </div>

  <p class="brand">Velstride Builders</p>

  <div class="contact">
    <p class="contact__social"><span class="contact__dot"></span>velstridebuilders</p>
    <p class="contact__web">www.velstridebuilders.com</p>
  </div>

  <div class="base-bar"></div>
</main>
</body>
</html>
```